Web Site Design for a Finance (lending) Company

We are opening a new subsidiary that focuses on lending money in the real estate industry. We need a web site designed to represent the business.

The business is lending money to real estate investors. A typical client/borrower will be looking to borrow money to buy a house, renovate it and then sell it at a profit, all within 12 months or less.

Company name is RTV Finance. Our logo is attached.

Attached is a general outline for the web site. We're working on writing more text for each page but this should give you enough to get started with some ideas.

Competitor web site that I like a lot (as an example): https://dorvaleqcapital.example/. Many of the general items on this site match what we will need (description of loan programs, FAQ)

Target Market(s)

Real estate investors (generally individuals or small companies with just a few people) who are buying homes, renovating them and then selling them at a profit.

Industry/Entity Type

Finance

Coding

Coded - Design and coding required

Number of Pages Required

5+ page

Colors

Designer to choose colors to be used in the design.

Requirements
Must have
• Minimalist design. Clean lines without too much clutter. Some stock photography is ok but the photos should not be distracting. They should almost fade in to the background so that user can focus on the key information about what our company does instead. We are a finance company, not a design company, so the information about our products will be more interesting to site visitors than the art.
• Some minimalist examples from Snapboard:
• https://www.snapboardia.example/explore/minimalist-web-design/
Nice to have
• If you search in zoovle for "hard money lenders" you will find many examples of web sites from our competition. I have provided a link above to competitor web site that I like a lot.
• I have attached our logo in EPS format. Logo is green. Web site doesn't have to be green but it should be of a color that will work well with the logo.

```html
<!DOCTYPE html>
<html lang="en">
<head>
<meta charset="utf-8">
<title>RTV Finance</title>
<link rel="stylesheet" href="https://fonts.googleapis.com/css2?family=Open+Sans:wght@400;600&family=Roboto+Condensed:wght@400;700&display=swap">
<style>
:root{
  --green:#0b4f30;
  --green-dark:#073b23;
  --green-deep:#052f1b;
  --accent:#1f9a6c;
  --ink:#2d2d2d;
  --muted:#555;
  --line:#e1e1e1;
  --soft:#f5f5f5;
  --white:#fff;
}
*{margin:0;padding:0;box-sizing:border-box}
html,body{width:1200px;height:3689px;overflow:hidden}
body{position:relative;background:var(--white);font-family:"Open Sans",Arial,sans-serif;color:var(--ink)}
.abs{position:absolute}
.heading{font-family:"Roboto Condensed","Arial Narrow",sans-serif;font-weight:400}

/* header */
.brand{display:flex;align-items:center;gap:14px}
.brand-mark{width:40px;height:40px;background:var(--green)}
.brand-name{font-family:"Open Sans",Arial,sans-serif;font-weight:600;font-size:30px;color:var(--green);line-height:1}
.contact-chip{display:flex;align-items:center;gap:12px;font-size:17px;color:var(--ink);white-space:nowrap}
.chip-icon{width:34px;height:34px;border:2px solid var(--green);border-radius:50%;display:flex;align-items:center;justify-content:center;flex:none}
.chat-btn{left:1018px;top:32px;width:91px;height:32px;border:2px solid var(--green);border-radius:16px;font-size:16px;color:var(--green);display:flex;align-items:center;justify-content:center;gap:6px}
.nav a{position:absolute;top:88px;font-size:18px;color:var(--ink);text-decoration:none}
.nav a.current{color:var(--green)}

/* hero */
.hero{left:0;top:140px;width:1200px;height:627px;overflow:hidden}
.hero-photo{position:absolute;inset:0;background:linear-gradient(100deg,#5b4a3c 0%,#8f7a63 35%,#b9b0a2 60%,#c9b68a 80%,#6f7b4a 100%)}
.hero-shade{position:absolute;inset:0;background:rgba(0,0,0,.18)}
.hero-title{position:absolute;left:0;width:1200px;top:208px;text-align:center;color:var(--white);font-family:"Open Sans",Arial,sans-serif;font-size:58px;font-weight:400}
.hero-sub{position:absolute;left:0;width:1200px;top:288px;text-align:center;color:var(--white);font-family:"Roboto Condensed","Arial Narrow",sans-serif;font-size:28px;line-height:39px}
.hero-arrow{position:absolute;top:293px;width:26px;height:26px;border-radius:50%;background:rgba(0,0,0,.55)}
.hero-curve{position:absolute;left:0;bottom:0}

/* loans */
.section-title{position:absolute;left:0;width:1200px;text-align:center;font-size:34px}
.loan-frame{background:var(--green)}
.loan-photo{box-shadow:0 8px 20px rgba(0,0,0,.25)}
.loan-title{font-size:29px}
.bullets{list-style:none;font-size:15.5px;color:var(--muted);line-height:22px}
.bullets li{position:relative;padding-left:24px}
.bullets li::before{content:"»";position:absolute;left:0;top:-1px;color:var(--ink)}

/* why */
.why{left:0;top:1704px;width:1200px;height:480px;background:linear-gradient(135deg,var(--green-dark),var(--green) 45%,var(--green-deep))}
.why .section-title{color:var(--white);top:72px}
.feature{position:absolute;top:173px;width:250px;text-align:center;color:var(--white)}
.feature-icon{width:112px;height:112px;margin:0 auto;border:3px solid var(--white);border-radius:50%;display:flex;align-items:center;justify-content:center}
.feature-name{font-size:18px;margin-top:32px}
.feature-text{font-size:13px;line-height:20px;margin-top:10px}
.why-arrow{position:absolute;top:232px;width:42px;height:42px;border-radius:50%;background:#0f6a3c;display:flex;align-items:center;justify-content:center}

/* about */
.about-art{left:111px;top:2312px;width:393px;height:307px;border-radius:8px;background:linear-gradient(160deg,#f3c76a 0%,#e9d9b3 45%,#9fc3d8 100%)}
.about-title{left:548px;top:2320px;font-size:36px}
.about-text{left:548px;top:2372px;width:516px;font-size:14px;line-height:21.7px;color:var(--muted);text-align:justify}
.btn-more{left:548px;top:2577px;width:106px;height:27px;border-radius:14px;background:var(--accent);color:var(--white);font-size:13px;display:flex;align-items:center;justify-content:center}

/* testimonial */
.testimonial{left:0;top:2750px;width:1200px;height:440px;background:linear-gradient(135deg,var(--green-dark),var(--green) 50%,var(--green-deep))}
.testimonial .section-title{color:var(--white);top:70px}
.quote{position:absolute;left:190px;width:820px;top:142px;text-align:center;color:var(--white);font-size:14px;line-height:27.5px}
.quote-mark{position:absolute;color:var(--white);font-size:34px;font-family:Georgia,serif}
.avatar{position:absolute;left:549px;top:231px;width:98px;height:98px;border-radius:50%;border:3px solid var(--white);background:linear-gradient(160deg,#d9c3a7,#8a6b52)}
.t-arrow{position:absolute;top:265px}
.author{position:absolute;left:0;width:1200px;top:344px;text-align:center;color:var(--white);font-style:italic;font-size:16px}

/* partners */
.partners{left:0;top:3190px;width:1200px;height:206px;background:var(--soft)}
.badge{position:absolute;top:51px;width:190px;height:109px;border:1px solid var(--line);border-radius:4px;background:#fafafa;display:flex;align-items:center;justify-content:center}
.badge span{width:110px;height:22px;border-radius:3px;background:#d6d6d6}

/* footer */
.foot-title{font-size:16px;letter-spacing:.5px;color:var(--ink)}
.foot-text{font-size:13px;line-height:21px;color:var(--muted)}
.subscribe{display:flex;left:652px;top:3540px}
.subscribe .field{width:146px;height:30px;border:1px solid #bbb;font-size:12px;color:#999;padding:6px 8px}
.subscribe .send{width:72px;height:30px;background:var(--green);color:var(--white);font-size:13px;display:flex;align-items:center;justify-content:center}
.social{display:flex;gap:14px;left:950px;top:3505px}
.social span{width:24px;height:24px;border-radius:4px;background:#555}
.foot-rule{left:86px;top:3620px;width:1028px;height:1px;background:var(--line)}
.copyright{left:0;width:1200px;top:3654px;text-align:center;font-size:12px;color:var(--muted)}
</style>
</head>
<body>

<!-- header -->
<div class="abs brand" style="left:86px;top:40px">
  <span class="brand-mark"></span><span class="brand-name">RTV Finance</span>
</div>
<div class="abs contact-chip" style="left:610px;top:30px">
  <span class="chip-icon"><svg width="16" height="16" viewBox="0 0 24 24"><path fill="#0b4f30" d="M6.6 10.8a15 15 0 0 0 6.6 6.6l2.2-2.2a1 1 0 0 1 1-.25 11.4 11.4 0 0 0 3.6.6 1 1 0 0 1 1 1V20a1 1 0 0 1-1 1A17 17 0 0 1 3 4a1 1 0 0 1 1-1h3.5a1 1 0 0 1 1 1c0 1.25.2 2.45.6 3.6a1 1 0 0 1-.25 1z"/></svg></span>
  555.014.2290
</div>
<div class="abs contact-chip" style="left:795px;top:30px">
  <span class="chip-icon"><svg width="16" height="16" viewBox="0 0 24 24"><path fill="#0b4f30" d="M3 5h18v14H3zm2 2v.5l7 4.5 7-4.5V7zm0 3v7h14v-7l-7 4.5z"/></svg></span>
  info@rtv.example
</div>
<div class="abs chat-btn"><svg width="14" height="14" viewBox="0 0 24 24"><path fill="none" stroke="#0b4f30" stroke-width="2.5" d="M4 14v-2a8 8 0 0 1 16 0v2M4 14h3v5H4zM17 14h3v5h-3z"/></svg>Chat</div>
<nav class="nav">
  <a class="current" href="#" style="left:507px">Home</a>
  <a href="#" style="left:614px">Aboutus</a>
  <a href="#" style="left:757px">Loans</a>
  <a href="#" style="left:873px">Resources</a>
  <a href="#" style="left:1022px">Contact Us</a>
</nav>

<!-- hero -->
<section class="abs hero">
  <div class="hero-photo" role="img" aria-label="Photo of three people reviewing loan documents together on a sofa"></div>
  <div class="hero-shade"></div>
  <h1 class="hero-title">RTV Finance</h1>
  <p class="hero-sub">Local real estate experts lending<br>to local real estate investors</p>
  <span class="hero-arrow" style="left:42px"><svg width="26" height="26"><path d="M15 8l-5 5 5 5" fill="none" stroke="#fff" stroke-width="2"/></svg></span>
  <span class="hero-arrow" style="left:1114px"><svg width="26" height="26"><path d="M11 8l5 5-5 5" fill="none" stroke="#fff" stroke-width="2"/></svg></span>
  <svg class="hero-curve" width="1200" height="110" viewBox="0 0 1200 110">
    <path d="M0 90 Q600 -10 1200 90 L1200 110 L0 110z" fill="#0b4f30"/>
    <path d="M0 106 Q600 6 1200 106 L1200 110 L0 110z" fill="#fff"/>
  </svg>
</section>

<!-- loans -->
<h2 class="section-title heading" style="top:804px">Loans offered</h2>

<div class="abs loan-frame" style="left:108px;top:927px;width:327px;height:285px"></div>
<div class="abs loan-photo" role="img" aria-label="Photo of a hand passing a money bag above a small model house" style="left:125px;top:944px;width:325px;height:293px;background:linear-gradient(135deg,#6e8a3a,#b7c46a 45%,#e4e0cf 75%,#c99a62)"></div>
<h3 class="abs loan-title heading" style="left:494px;top:980px">Fix and Flip Loans</h3>
<ul class="abs bullets" style="left:494px;top:1041px;width:620px">
  <li>Description of the loan type, borrower requirements</li>
  <li style="margin-top:11px">Loan terms table (fee, rate, loan to cost etc.) [Let me know if you want this and what info you want to include on the website]</li>
  <li style="margin-top:12px">Why choose RTV</li>
  <li style="margin-top:12px">Online application or Contact web form [Do you want application or just contact us webform? If application, we'll need to know what fields should be included]</li>
</ul>

<h3 class="abs loan-title heading" style="left:106px;top:1357px">Commercial Hard Money Loans</h3>
<ul class="abs bullets" style="left:106px;top:1415px;width:600px">
  <li>Description of the loan type, borrower requirements</li>
  <li style="margin-top:20px">Loan terms table (fee, rate, loan to cost etc.)</li>
  <li style="margin-top:18px">Why choose RTV</li>
  <li style="margin-top:18px">Online application or Contact web form [Do you want application or just contact us webform? If application, we'll need to know what fields should be included]</li>
</ul>
<div class="abs loan-frame" style="left:740px;top:1311px;width:342px;height:290px"></div>
<div class="abs loan-photo" role="img" aria-label="Photo of a model house beside stacked coins and a growing plant" style="left:730px;top:1328px;width:337px;height:295px;background:linear-gradient(180deg,#f3efe6 0%,#d9c9a4 55%,#8a6a3e 100%)"></div>

<!-- why borrow -->
<section class="abs why">
  <h2 class="section-title heading">Why borrow from RTV</h2>
  <span class="why-arrow" style="left:36px"><svg width="16" height="16"><path d="M10 3l-5 5 5 5" fill="none" stroke="#1b1b1b" stroke-width="2"/></svg></span>
  <span class="why-arrow" style="left:1118px"><svg width="16" height="16"><path d="M6 3l5 5-5 5" fill="none" stroke="#1b1b1b" stroke-width="2"/></svg></span>
  <div class="feature" style="left:74px">
    <div class="feature-icon"><svg width="48" height="40" viewBox="0 0 48 40" fill="#fff"><circle cx="24" cy="10" r="7"/><path d="M12 36c0-8 5-13 12-13s12 5 12 13z"/><circle cx="9" cy="14" r="5"/><path d="M0 34c0-6 4-10 9-10 2 0 3 .5 4 1-2 3-3 6-3 9z"/><circle cx="39" cy="14" r="5"/><path d="M48 34c0-6-4-10-9-10-2 0-3 .5-4 1 2 3 3 6 3 9z"/></svg></div>
    <div class="feature-name">Experts</div>
    <p class="feature-text">It is a long established fact that<br>a reader will be distracted</p>
  </div>
  <div class="feature" style="left:342px">
    <div class="feature-icon"><svg width="44" height="44" viewBox="0 0 44 44" fill="none" stroke="#fff" stroke-width="3"><rect x="5" y="9" width="28" height="28" rx="3"/><path d="M16 26l2-6 16-16 4 4-16 16z" fill="#fff"/></svg></div>
    <div class="feature-name">Fast Approval</div>
    <p class="feature-text">It is a long established fact that<br>a reader will be distracted</p>
  </div>
  <div class="feature" style="left:605px">
    <div class="feature-icon"><svg width="34" height="44" viewBox="0 0 34 44" fill="none" stroke="#fff" stroke-width="3"><path d="M11 30c0-5-7-8-7-16a13 13 0 0 1 26 0c0 8-7 11-7 16z"/><path d="M12 35h10M13 40h8"/></svg></div>
    <div class="feature-name">Professional</div>
    <p class="feature-text">It is a long established fact that<br>a reader will be distracted</p>
  </div>
  <div class="feature" style="left:871px">
    <div class="feature-icon"><svg width="44" height="44" viewBox="0 0 44 44"><circle cx="18" cy="18" r="13" fill="#fff"/><path d="M27 27l12 12" stroke="#fff" stroke-width="6" stroke-linecap="round"/><path d="M18 11v14M11 18h14" stroke="#0b4f30" stroke-width="3.5"/></svg></div>
    <div class="feature-name">Selective</div>
    <p class="feature-text">It is a long established fact that<br>a reader will be distracted</p>
  </div>
</section>

<!-- about -->
<div class="abs about-art" role="img" aria-label="Illustration of a small house on documents with keys, coins and a calculator"></div>
<h2 class="abs about-title heading">About us</h2>
<p class="abs about-text">RTV Finance is a local business with local knowledge and strong industry relationships. A partner with a wide network who offers value added services. RTV has an established pool of experienced investors available for your real estate investment needs RTV Finance is a local business with local knowledge and strong industry relationships. A partner with a wide network who offers value added services. RTV has an established pool of experienced investors available for your real estate investment needs.</p>
<div class="abs btn-more">Read More</div>

<!-- testimonial -->
<section class="abs testimonial">
  <h2 class="section-title heading">Testimonial</h2>
  <span class="quote-mark" style="left:160px;top:130px">&ldquo;</span>
  <p class="quote">It is a long established fact that a reader will be distracted by the readable content of a page when looking at its layout. The point of using Lorem Ipsum is that it has a more-or-less normal distribution of letters, as opposed to using 'Content here, content here', making it look like readable English. Many desktop publishing packages and web page editors</p>
  <span class="quote-mark" style="left:960px;top:192px">&rdquo;</span>
  <svg class="t-arrow" style="left:506px" width="18" height="28"><path d="M14 3L4 14l10 11" fill="none" stroke="#fff" stroke-width="2.5"/></svg>
  <div class="avatar" role="img" aria-label="Portrait photo of the reviewer"></div>
  <svg class="t-arrow" style="left:672px" width="18" height="28"><path d="M4 3l10 11L4 25" fill="none" stroke="#fff" stroke-width="2.5"/></svg>
  <p class="author">Dolorem ipsum</p>
</section>

<!-- partners -->
<section class="abs partners" aria-label="Partners">
  <div class="badge" style="left:96px"><span></span></div>
  <div class="badge" style="left:302px"><span></span></div>
  <div class="badge" style="left:507px"><span></span></div>
  <div class="badge" style="left:711px"><span></span></div>
  <div class="badge" style="left:915px"><span></span></div>
</section>

<!-- footer -->
<div class="abs brand" style="left:86px;top:3516px">
  <span class="brand-mark"></span><span class="brand-name">RTV Finance</span>
</div>
<h4 class="abs foot-title heading" style="left:352px;top:3456px">CONTACT US</h4>
<p class="abs foot-text" style="left:352px;top:3496px">Address : 12 Harlow Lane, Eastbury,<br>Ks4 8PL<br>Phone : 01632 960 418<br>Email : info@rtv.example</p>
<h4 class="abs foot-title heading" style="left:652px;top:3456px">JOIN OUR MAILING LIST</h4>
<p class="abs foot-text" style="left:652px;top:3492px;width:230px;font-size:12px;line-height:18px">Your about us information would fit here nicely.</p>
<div class="abs subscribe"><div class="field">Email address</div><div class="send">Submit</div></div>
<h4 class="abs foot-title heading" style="left:950px;top:3456px">FOLLOW US OUT THERE</h4>
<div class="abs social" aria-label="Social links"><span></span><span></span><span></span><span></span></div>
<div class="abs foot-rule"></div>
<p class="abs copyright">Copyright © 2017. All Rights Reserved</p>

</body>
</html>
```